Business Cards for new orthopaedic surgery practice

My husband and I are starting our own orthopaedic surgery practice. We are looking for a business card that is uniform, but one will have my name/title and the other will have his. You can just create one design with my name on it for now. But when I choose your design as the winning design I will ask that you add another copy with his name/title.

We are looking for classy, simple, elite all in one. We like dark blues/a little gold/yellow. Something that goes with our logo. We want our logo incorporated. Here is all the info you need:
Business name: RV Bone & Vitality Center
Location: 38517 North Willowmere Ave
Palm Hollow, FL 33490
Phone: 954-218-4063
Fax: 954-582-7341
Email: info@myrvbonecare.example

Names: Lydia Vance, M.D.
Board Certified Hand and Upper Extremity Surgeon

Ebo Dansu, M.D.
Board Certified Hip & Knee Replacement/General Orthopaedic Surgeon

Can decide what you want to put on the back. Maybe a slogan:
Grounded in Skill. Centered on You

I am just going to upload our logo. The only thing is if we select you as the winning design, the location, and phone numbers may change. We will need your help to update that once fully solidified.

Industry/Entity Type

Medical

Contact Information for Business Card

Colors
0054AA
0677BA
7BADD7
CADEEF
E8F1F8
0094D4
00A9DD
6FCCEA
C7EBF8
E9F6FB

Requirements
Must have
• class, appeal,
Should not have
• We want to air on the side of masculine if we are looking at masculine vs. feminine feel. But we still want it classy, sophisticated, and something we will love

```html
<!DOCTYPE html>
<html lang="en">
<head>
<meta charset="utf-8">
<title>RV Bone &amp; Vitality Center — Business Card</title>
<link rel="stylesheet" href="https://fonts.googleapis.com/css2?family=Libre+Baskerville:wght@400;700&family=Figtree:wght@400;500&display=swap">
<style>
  :root {
    --backdrop: #1c1c1e;
    --navy: #1b2a52;
    --navy-soft: #2d4276;
    --paper: #f3f3f2;
    --gold: #c59a4e;
    --ink-light: #ffffff;
  }
  * { margin: 0; padding: 0; box-sizing: border-box; }
  html, body { width: 1200px; height: 1059px; overflow: hidden; }
  body { background: var(--backdrop); position: relative; font-family: "Figtree", sans-serif; }

  .card {
    position: absolute;
    width: 690px;
    height: 391px;
    border-radius: 18px;
    overflow: hidden;
    background: var(--navy);
    box-shadow: 0 12px 30px rgba(0,0,0,.55);
  }
  .card--front { left: 256px; top: 89px; }
  .card--back { left: 255px; top: 548px; }

  .front-shape { position: absolute; inset: 0; width: 100%; height: 100%; }

  .contact { position: absolute; left: 40px; top: 130px; color: var(--ink-light); }
  .contact__name {
    font-family: "Libre Baskerville", serif;
    font-weight: 700;
    font-size: 19px;
    color: var(--gold);
    letter-spacing: .2px;
  }
  .contact__title { font-size: 15.5px; line-height: 21px; margin-top: 2px; }
  .contact__address { font-size: 16px; line-height: 23px; margin-top: 17px; }
  .contact__lines { list-style: none; margin-top: 14px; }
  .contact__lines li { display: flex; align-items: center; font-size: 16px; height: 27px; }
  .contact__lines svg { width: 13px; height: 13px; margin-right: 8px; fill: var(--gold); flex: none; }

  .brand-name {
    position: absolute;
    left: 460px; top: 100px; width: 200px;
    text-align: center;
    font-family: "Libre Baskerville", serif;
    font-weight: 700;
    font-size: 24px;
    line-height: 32px;
    color: var(--navy);
  }

  .brand-name--faint {
    left: 195px; top: 130px; width: 300px;
    font-size: 30px; line-height: 40px;
    color: var(--navy-soft);
  }

  .tagline {
    position: absolute;
    left: 0; right: 0; top: 332px;
    text-align: center;
    font-size: 21px;
    font-weight: 500;
    color: var(--gold);
  }
</style>
</head>
<body>

<section class="card card--front">
  <svg class="front-shape" viewBox="0 0 690 391" preserveAspectRatio="none" aria-hidden="true">
    <path d="M222 0 C 262 205 440 318 690 326 L690 0 Z" fill="var(--gold)"/>
    <path d="M230 0 C 268 202 446 312 690 326 L690 0 Z" fill="#ffffff"/>
    <path d="M234 0 C 272 200 448 310 690 326 L690 0 Z" fill="var(--paper)"/>
  </svg>

  <div class="brand-name">RV Bone &amp;<br>Vitality Center</div>

  <div class="contact">
    <h1 class="contact__name">LYDIA VANCE, M.D.</h1>
    <p class="contact__title">Board Certified Hand and<br>Upper Extremity Surgeon</p>
    <p class="contact__address">38517 North Willowmere Ave<br>Palm Hollow, FL 33490</p>
    <ul class="contact__lines">
      <li>
        <svg viewBox="0 0 16 16"><path d="M3.6 1 L6 3.6 4.7 5.4 C5.6 7.6 8.3 10.3 10.6 11.3 L12.4 10 15 12.4 13.4 14.6 C8 15 1 8 1.4 2.6 Z"/></svg>
        954-218-4063
      </li>
      <li>
        <svg viewBox="0 0 16 16"><path d="M4 1h8v4H4zM1 6h14v6h-3v3H4v-3H1zM5 10v4h6v-4z"/></svg>
        954-582-7341
      </li>
      <li>
        <svg viewBox="0 0 16 16"><path d="M1 3h14v10H1zM2.2 4.2 8 8.6l5.8-4.4v-.2H2.2zM2 5.4V12h12V5.4L8 10z"/></svg>
        info@myrvbonecare.example
      </li>
    </ul>
  </div>
</section>

<section class="card card--back">
  <div class="brand-name brand-name--faint">RV Bone &amp;<br>Vitality Center</div>
  <p class="tagline">Grounded in Skill. Centered on You</p>
</section>

</body>
</html>
```